Pellham Grove Trust - New Website Designed

I need a site that looks like this http://www.quorlandgiving.org for boat donations. So please replace the cars with boats.

```html
<!DOCTYPE html>
<html lang="en">
<head>
<meta charset="utf-8">
<title>Pellham Grove Trust – Donate Your Boat</title>
<link rel="stylesheet" href="https://fonts.googleapis.com/css2?family=Oswald:wght@500;600&family=Open+Sans:ital,wght@0,400;0,600;0,700;0,800;1,800&display=swap">
<style>
:root{
  --red:#d71a1f;
  --red-dark:#b3121a;
  --blue:#1b3fae;
  --blue-deep:#16318c;
  --navy:#0c1a3a;
  --green:#3fae2a;
  --grey-band:#e9e9e9;
  --card-grey:#ededed;
  --ink:#333333;
  --ink-soft:#555555;
  --white:#ffffff;
  --footer-dark:#4a4a4a;
}
*{margin:0;padding:0;box-sizing:border-box}
html,body{width:1200px;height:2452px;overflow:hidden}
body{position:relative;font-family:"Open Sans",Arial,sans-serif;color:var(--ink);background:var(--white)}
.abs{position:absolute}

/* header */
.site-header{left:0;top:0;width:1200px;height:106px;background:linear-gradient(90deg,#3a3f72,#6e5a78 45%,#a66c6e)}
.brand{left:75px;top:28px;font-family:"Oswald",sans-serif;font-weight:600;font-size:37px;color:var(--white);letter-spacing:.3px}
.main-nav{left:0;top:106px;width:1200px;height:52px;background:var(--blue)}
.main-nav a{position:absolute;top:16px;font-size:15.5px;font-weight:700;color:var(--white);text-decoration:none;letter-spacing:.4px}

/* hero */
.hero-photo{left:0;top:158px;width:1200px;height:496px;background:linear-gradient(90deg,#c9b39a 0%,#f2c8a6 30%,#f7d4bb 60%,#f9dcc6 100%)}

/* donate panel */
.donate-panel{left:767px;top:0;width:360px;height:640px}
.donate-call{left:788px;top:22px;width:330px;height:70px}
.donate-call .label{position:absolute;left:64px;top:0;font-size:17px;font-weight:700;color:var(--white);letter-spacing:.3px}
.donate-call .num{position:absolute;left:64px;top:17px;font-size:26px;font-weight:800;color:var(--white)}
.donate-call .hours{position:absolute;left:64px;top:52px;font-size:11.5px;font-weight:700;color:var(--white)}
.donate-title{left:767px;top:106px;width:360px;height:52px;text-align:center;font-family:"Oswald",sans-serif;font-weight:600;font-size:29px;line-height:52px;color:var(--white)}
.donate-sub{left:767px;top:172px;width:360px;text-align:center;font-size:15px;font-weight:700;color:var(--white)}
.field{position:absolute;height:34px;background:var(--white);border-radius:17px;font-size:13px;color:var(--ink-soft);padding:0 18px;line-height:34px}
.field.select::after{content:"";position:absolute;right:14px;top:10px;border:4px solid transparent;border-bottom-color:#555;height:0}
.field.select::before{content:"";position:absolute;right:14px;top:19px;border:4px solid transparent;border-top-color:#555;height:0}
.submit{left:795px;top:518px;width:297px;height:41px;border-radius:21px;background:var(--green);color:var(--white);font-size:16px;font-weight:700;text-align:center;line-height:41px;letter-spacing:.3px}

/* feature band */
.feature-band{left:0;top:654px;width:1200px;height:183px;background:var(--grey-band)}
.feature-slogan{left:0;top:632px;width:490px;height:205px}
.slogan-text{left:75px;top:674px;color:var(--white)}
.slogan-text .l1{font-size:31px;font-weight:800;letter-spacing:.5px}
.slogan-text .l2{font-size:54px;font-weight:800;font-style:italic;line-height:1.0}
.slogan-text .l3{font-size:31px;font-weight:800;letter-spacing:.5px;margin-top:4px}
.feature{position:absolute;top:700px;width:126px;text-align:center}
.feature svg{display:block;margin:0 auto 8px;height:56px}
.feature p{font-size:12.5px;font-weight:600;color:var(--blue);line-height:1.4}

/* how to donate */
.section-title{width:1200px;left:0;text-align:center;font-size:23px;font-weight:700;color:var(--ink);letter-spacing:.6px}
.step-card{position:absolute;top:937px;width:331px;height:253px;border-radius:12px;background:linear-gradient(180deg,#ffffff,#e6e6e6);overflow:hidden}
.step-card h3{height:47px;line-height:47px;text-align:center;color:var(--white);font-size:18px;font-weight:700;letter-spacing:.4px}
.step-card svg{display:block;margin:28px auto 0;height:96px}
.step-card p{position:absolute;left:20px;right:20px;top:192px;text-align:center;font-size:14.5px;line-height:1.5;color:var(--ink)}

/* why donate */
.why{left:0;top:1241px;width:1200px;height:415px;background:linear-gradient(90deg,#050b1a 0%,#0d1f4a 40%,#142b63 60%,#1b4a3a 85%,#0a1422 100%)}
.why-title{top:1290px;color:var(--white)}
.why-list{left:77px;top:1350px;list-style:none}
.why-list li{position:relative;padding-left:33px;height:35.2px;font-size:13.8px;color:var(--white)}
.why-list li svg{position:absolute;left:0;top:3px}

/* faq */
.faq-photo{left:0;top:1656px;width:526px;height:478px;background:linear-gradient(135deg,#8a5a3c 0%,#b99a7a 40%,#7e7a68 70%,#5b5a4c 100%)}
.faq-title{left:562px;top:1709px;font-size:23px;font-weight:700;letter-spacing:.6px;color:var(--ink)}
.faq-item{position:absolute;left:562px;width:565px;height:50px;border:1.5px solid #b8b8b8;border-radius:25px;font-size:14.5px;line-height:47px;padding-left:22px;color:var(--ink-soft)}
.faq-item::after{content:"";position:absolute;right:20px;top:17px;width:14px;height:14px;border-radius:2px;background:#333}
.faq-item::before{content:"+";position:absolute;right:20px;top:17px;width:14px;height:14px;line-height:13px;text-align:center;color:var(--white);font-weight:700;font-size:13px;z-index:1}

/* footer */
.site-footer{left:0;top:2134px;width:1200px;height:264px;background:linear-gradient(90deg,#8c0d12 0%,#c8151b 35%,var(--red) 100%)}
.footer-col h4{font-size:15px;font-weight:700;color:var(--white);letter-spacing:.6px;margin-bottom:14px}
.footer-col p{font-size:13px;line-height:1.55;color:var(--white)}
.footer-col a{display:block;font-size:13px;color:var(--white);text-decoration:none;margin-bottom:13px}
.footer-call{left:768px;top:2188px;width:360px;height:154px;background:var(--blue);border:3px solid var(--white);border-radius:4px}
.footer-call .label{position:absolute;left:84px;top:44px;font-size:17px;font-weight:700;color:var(--white)}
.footer-call .num{position:absolute;left:84px;top:62px;font-size:27px;font-weight:800;color:var(--white)}
.footer-call .hours{position:absolute;left:84px;top:98px;font-size:12px;font-weight:700;color:var(--white)}
.copyright{left:0;top:2398px;width:1200px;height:54px;background:var(--footer-dark);text-align:center;line-height:54px;font-size:13px;color:#e8e8e8}
</style>
</head>
<body>

<header class="site-header abs">
</header>
<div class="brand abs">PELLHAM GROVE TRUST</div>

<nav class="main-nav abs">
  <a href="#how" style="left:77px">HOW TO DONATE</a>
  <a href="#why" style="left:255px">WHY DONATE</a>
  <a href="#faq" style="left:405px">FAQ</a>
  <a href="#about" style="left:482px">ABOUT</a>
</nav>

<div class="hero-photo abs" role="img" aria-label="Photo of a uniformed service member hugging a young girl, beside two white and red motor boats"></div>

<!-- donate form panel -->
<svg class="donate-panel abs" viewBox="0 0 360 640" aria-hidden="true">
  <path d="M0 0H360V560Q180 670 0 560Z" fill="var(--red)"/>
  <rect x="0" y="0" width="360" height="106" fill="var(--red-dark)"/>
  <rect x="0" y="158" width="360" height="2" fill="#a50f15"/>
</svg>
<div class="donate-call abs">
  <svg class="abs" style="left:0;top:6px" width="48" height="48" viewBox="0 0 24 24"><path fill="#fff" d="M6.6 10.8a15.1 15.1 0 0 0 6.6 6.6l2.2-2.2a1 1 0 0 1 1-.25 11.4 11.4 0 0 0 3.6.57 1 1 0 0 1 1 1V20a1 1 0 0 1-1 1A17 17 0 0 1 3 4a1 1 0 0 1 1-1h3.5a1 1 0 0 1 1 1c0 1.25.2 2.45.57 3.57a1 1 0 0 1-.25 1z"/></svg>
  <div class="label">CALL TODAY TO DONATE</div>
  <div class="num">1-800-555-0148</div>
  <div class="hours">Live Operators Available - 7 Days A Week</div>
</div>
<div class="donate-title abs">DONATE YOUR BOAT ONLINE</div>
<div class="donate-sub abs">Full Tax Deduction - Running or Not</div>
<div class="field" style="left:795px;top:213px;width:297px">First Name</div>
<div class="field" style="left:795px;top:255px;width:297px">Last Name</div>
<div class="field" style="left:795px;top:298px;width:297px">Zip Code</div>
<div class="field" style="left:795px;top:340px;width:297px">Day Phone</div>
<div class="field" style="left:795px;top:383px;width:297px">Email Address</div>
<div class="field select" style="left:795px;top:425px;width:145px">Choose Year</div>
<div class="field select" style="left:947px;top:425px;width:145px">Choose Make</div>
<div class="field" style="left:795px;top:468px;width:297px">Model of Boat</div>
<div class="submit abs">SUBMIT APPLICATION</div>

<!-- feature band -->
<div class="feature-band abs"></div>
<svg class="feature-slogan abs" viewBox="0 0 490 205" aria-hidden="true"><path d="M0 0H465L490 205H0Z" fill="var(--blue)"/></svg>
<div class="slogan-text abs">
  <div class="l1">DONATE YOUR BOAT TO</div>
  <div class="l2">Veterans</div>
  <div class="l3">MAKE A DIFFERENCE</div>
</div>

<div class="feature" style="left:490px">
  <svg viewBox="0 0 56 56"><circle cx="28" cy="28" r="25" fill="none" stroke="#444" stroke-width="4"/><text x="28" y="39" text-anchor="middle" font-family="Open Sans,sans-serif" font-weight="700" font-size="32" fill="#444">$</text><line x1="11" y1="11" x2="45" y2="45" stroke="#444" stroke-width="4"/></svg>
  <p>You have<br>no costs</p>
</div>
<div class="feature" style="left:617px">
  <svg viewBox="0 0 90 56"><rect x="4" y="26" width="54" height="16" fill="#444"/><path d="M10 26V14H30L38 26Z" fill="#444"/><rect x="15" y="17" width="12" height="8" fill="#fff"/><path d="M58 34L82 10" stroke="#444" stroke-width="4"/><path d="M82 10V28" stroke="#444" stroke-width="2"/><circle cx="18" cy="44" r="7" fill="#444" stroke="#fff" stroke-width="2"/><circle cx="48" cy="44" r="7" fill="#444" stroke="#fff" stroke-width="2"/></svg>
  <p>Free towing,<br>running or not</p>
</div>
<div class="feature" style="left:746px">
  <svg viewBox="0 0 44 56"><path d="M4 4H30L40 14V52H4Z" fill="none" stroke="#444" stroke-width="3"/><text x="20" y="24" text-anchor="middle" font-family="Open Sans,sans-serif" font-weight="700" font-size="10" fill="#444">TAX</text><path d="M10 32H34M10 39H28" stroke="#444" stroke-width="2"/><path d="M26 46L31 50L40 38" stroke="#444" stroke-width="3" fill="none"/></svg>
  <p>We issue you an<br>IRS tax receipt</p>
</div>
<div class="feature" style="left:874px">
  <svg viewBox="0 0 44 56"><path d="M4 2H28L40 14V54H4Z" fill="#444"/><path d="M28 2V14H40" fill="#777"/><path d="M11 24H33M11 32H33M11 40H33" stroke="#fff" stroke-width="3"/></svg>
  <p>We take care of<br>all paperwork</p>
</div>
<div class="feature" style="left:1001px">
  <svg viewBox="0 0 100 56"><path d="M4 30H92L80 44H18Z" fill="#444"/><path d="M30 30L42 20H70L76 30" fill="none" stroke="#444" stroke-width="3"/><path d="M4 30L96 24" stroke="#444" stroke-width="2"/></svg>
  <p>We take care of<br>DMV &amp; Smog issues</p>
</div>

<!-- how to donate -->
<h2 id="how" class="section-title abs" style="top:880px">HOW TO DONATE</h2>

<div class="step-card" style="left:75px">
  <h3 style="background:var(--red)">CALL OR FILL FORM</h3>
  <svg viewBox="0 0 110 96"><rect x="5" y="4" width="100" height="70" rx="4" fill="#444"/><rect x="13" y="12" width="84" height="54" fill="#fff"/><rect x="22" y="20" width="40" height="24" fill="#444"/><path d="M68 22H88M68 30H88M68 38H88M22 52H88" stroke="#444" stroke-width="3"/><rect x="45" y="74" width="20" height="10" fill="#444"/><rect x="30" y="84" width="50" height="6" fill="#444"/></svg>
  <p>Call us at 1-800-555-0172 or<br>Fill out the online form</p>
</div>
<div class="step-card" style="left:435px">
  <h3 style="background:var(--blue)">WE TOW BOAT FREE</h3>
  <svg viewBox="0 0 230 96"><rect x="6" y="46" width="74" height="22" fill="#444"/><path d="M14 46V28H42L54 46Z" fill="#444"/><rect x="22" y="32" width="16" height="11" fill="#fff"/><path d="M80 58L112 28" stroke="#444" stroke-width="5"/><path d="M112 28V50" stroke="#444" stroke-width="2"/><circle cx="26" cy="70" r="10" fill="#444" stroke="#fff" stroke-width="3"/><circle cx="64" cy="70" r="10" fill="#444" stroke="#fff" stroke-width="3"/><path d="M104 52L222 62L206 82H120Z" fill="#444"/><path d="M140 54L156 40H190L200 58" fill="none" stroke="#444" stroke-width="4"/><path d="M112 78H200" stroke="#444" stroke-width="3"/><circle cx="150" cy="84" r="7" fill="#444" stroke="#fff" stroke-width="2"/></svg>
  <p>Donate you boat and arrange for easy<br>pick-up and free towing.</p>
</div>
<div class="step-card" style="left:796px">
  <h3 style="background:#555555">TAX WRITE OFF</h3>
  <svg viewBox="0 0 90 96"><rect x="10" y="8" width="64" height="84" rx="3" fill="none" stroke="#444" stroke-width="4"/><rect x="28" y="2" width="28" height="12" rx="3" fill="#444"/><text x="42" y="40" text-anchor="middle" font-family="Open Sans,sans-serif" font-weight="700" font-size="16" fill="#444">TAX</text><path d="M20 52H56M20 62H52M20 72H46" stroke="#444" stroke-width="3"/><path d="M56 80L84 30L88 34L62 84Z" fill="#444"/></svg>
  <p>You will receive your tax deductible<br>boat donation receipt.</p>
</div>

<!-- why donate -->
<section id="why" class="why abs" role="img" aria-label="Photo of a saluting soldier silhouetted against a waving flag"></section>
<h2 class="section-title why-title abs">WHY DONATE YOUR BOAT TO US</h2>
<ul class="why-list abs">
  <li><svg width="14" height="14" viewBox="0 0 14 14"><circle cx="7" cy="7" r="7" fill="#fff"/><path d="M3.5 7.2L6 9.5L10.5 4.5" stroke="#0c1a3a" stroke-width="2" fill="none"/></svg>Civic Trust Bureau A+ Rated &amp; IRS 501(c)3 Approved : Free 24/7 Pickup with No DMV Hassles.</li>
  <li><svg width="14" height="14" viewBox="0 0 14 14"><circle cx="7" cy="7" r="7" fill="#fff"/><path d="M3.5 7.2L6 9.5L10.5 4.5" stroke="#0c1a3a" stroke-width="2" fill="none"/></svg>Free Local Towing : We will pick up your car donation, running or not, when it's most convenient, at home or work.</li>
  <li><svg width="14" height="14" viewBox="0 0 14 14"><circle cx="7" cy="7" r="7" fill="#fff"/><path d="M3.5 7.2L6 9.5L10.5 4.5" stroke="#0c1a3a" stroke-width="2" fill="none"/></svg>All Boats Accepted : We take your car regardless of its condition or registration status.</li>
  <li><svg width="14" height="14" viewBox="0 0 14 14"><circle cx="7" cy="7" r="7" fill="#fff"/><path d="M3.5 7.2L6 9.5L10.5 4.5" stroke="#0c1a3a" stroke-width="2" fill="none"/></svg>Income Tax Deduction : We issue you an IRS tax receipt &amp; offer the largest resale network to get you the highest tax write-off possible.</li>
  <li><svg width="14" height="14" viewBox="0 0 14 14"><circle cx="7" cy="7" r="7" fill="#fff"/><path d="M3.5 7.2L6 9.5L10.5 4.5" stroke="#0c1a3a" stroke-width="2" fill="none"/></svg>No Paperwork Hassles : We take any car and handle everything: DMV, Smog and IRS paperwork.</li>
  <li><svg width="14" height="14" viewBox="0 0 14 14"><circle cx="7" cy="7" r="7" fill="#fff"/><path d="M3.5 7.2L6 9.5L10.5 4.5" stroke="#0c1a3a" stroke-width="2" fill="none"/></svg>Boat donations help fund programs : And benefit Allied Service Members Fund. An IRS 501(c)3 nonprofit organization.</li>
  <li><svg width="14" height="14" viewBox="0 0 14 14"><circle cx="7" cy="7" r="7" fill="#fff"/><path d="M3.5 7.2L6 9.5L10.5 4.5" stroke="#0c1a3a" stroke-width="2" fill="none"/></svg>Schedule a Free Pickup : Complete the form and a representative will call you to arrange a convenient time to pickup your Boat.</li>
</ul>

<!-- faq -->
<div class="faq-photo abs" role="img" aria-label="Photo of a smiling soldier with his daughter on his back, flag on the porch behind them"></div>
<h2 id="faq" class="faq-title abs">FREQUENTLY ASKED QUESTIONS</h2>
<div class="faq-item" style="top:1772px">Nam fermentum vestibulum purus id aliquet.?</div>
<div class="faq-item" style="top:1834px">Nam fermentum vestibulum purus id aliquet.?</div>
<div class="faq-item" style="top:1896px">Nam fermentum vestibulum purus id aliquet.?</div>
<div class="faq-item" style="top:1958px">Nam fermentum vestibulum purus id aliquet.?</div>
<div class="faq-item" style="top:2021px">Nam fermentum vestibulum purus id aliquet.?</div>

<!-- footer -->
<footer class="site-footer abs"></footer>
<div id="about" class="footer-col abs" style="left:75px;top:2186px;width:250px">
  <h4>ABOUT PELLHAM GROVE TRUST</h4>
  <p>Vestibulum vel metus sit amet turpis bibendum tincidunt vel sit amet quam. Pellentesque habitant morbi tristique senectus et netus et male-suada fames ac .</p>
</div>
<div class="footer-col abs" style="left:381px;top:2186px">
  <h4>NAVIGATION</h4>
  <a href="#how">How To Donate</a>
  <a href="#why">Why Donate</a>
  <a href="#faq">Faq</a>
  <a href="#about">About</a>
</div>
<div class="footer-col abs" style="left:564px;top:2186px">
  <h4>SAFE &amp; SEQURE</h4>
  <svg width="120" height="110" viewBox="0 0 120 110" aria-hidden="true">
    <rect x="0" y="6" width="110" height="40" rx="5" fill="#ffffff" opacity=".9"/>
    <circle cx="24" cy="90" r="18" fill="#ffffff" opacity=".9"/>
  </svg>
</div>
<div class="footer-call abs">
  <svg class="abs" style="left:18px;top:46px" width="52" height="52" viewBox="0 0 24 24"><path fill="#fff" d="M6.6 10.8a15.1 15.1 0 0 0 6.6 6.6l2.2-2.2a1 1 0 0 1 1-.25 11.4 11.4 0 0 0 3.6.57 1 1 0 0 1 1 1V20a1 1 0 0 1-1 1A17 17 0 0 1 3 4a1 1 0 0 1 1-1h3.5a1 1 0 0 1 1 1c0 1.25.2 2.45.57 3.57a1 1 0 0 1-.25 1z"/></svg>
  <div class="label">CALL TODAY TO DONATE</div>
  <div class="num">1-800-555-0148</div>
  <div class="hours">Live Operators Available - 7 Days A Week</div>
</div>
<div class="copyright abs">Copyright © 2017 Pellham Grove Trust. Privacy Policy. All Rights Reserved.</div>

</body>
</html>
```